BUSINESS CARD DESIGN

NAME- DALE VORSKIN
PHONE NUMER - 555- 714-9082
EMAIL- OFFICE@TRV-GROUNDMAKRZ.COM
BACK OF CARD- SPEACIALIZES IN LAND CLEARING, FORESTRY MUCLHING AND EXCAVATION

Contact Information for Business Card

NAME- DALE VORSKIN PHONE NUMER - 555- 714-9082 EMAIL- OFFICE@TRV-GROUNDMAKRZ.COM BACK OF CARD- SPEACIALIZES IN LAND CLEARING , MUCLHING AND EXCAVATION

```html
<!DOCTYPE html>
<html lang="en">
<head>
<meta charset="utf-8">
<title>Business Card – Trevan Groundmakrz</title>
<link href="https://fonts.googleapis.com/css2?family=Montserrat:wght@600;700&display=swap" rel="stylesheet">
<style>
  :root {
    --gold: #f5b414;
    --ink: #000000;
    --paper: #ffffff;
    --page: #ffffff;
  }
  * { margin: 0; padding: 0; box-sizing: border-box; }
  html, body { width: 1200px; height: 1131px; overflow: hidden; background: var(--page); }
  body { position: relative; font-family: "Montserrat", sans-serif; color: var(--gold); }

  .card { position: absolute; left: 256px; width: 689px; height: 394px; overflow: hidden; }
  .card--front { top: 151px; background: var(--paper); }
  .card--back { top: 627px; background: var(--ink); }

  .front-wave { position: absolute; left: 0; top: 0; width: 689px; height: 394px; }

  .brand { position: absolute; display: flex; flex-direction: column; align-items: center; text-align: center; font-weight: 700; color: var(--gold); }
  .brand__dot { border-radius: 50%; background: var(--gold); }
  .brand__name { letter-spacing: 0.06em; line-height: 1.25; }

  .card--front .brand { left: 53px; top: 90px; width: 206px; }
  .card--front .brand__dot { width: 96px; height: 96px; margin-bottom: 18px; }
  .card--front .brand__name { font-size: 15px; }

  .divider { position: absolute; left: 321px; top: 75px; width: 3px; height: 220px; background: var(--gold); }

  .person { position: absolute; left: 375px; top: 72px; }
  .person__name { font-size: 32px; font-weight: 700; letter-spacing: 0.01em; line-height: 1.1; }
  .person__role { display: inline-block; margin-top: 4px; font-size: 22px; font-weight: 600; padding-bottom: 2px; border-bottom: 3px solid var(--gold); }

  .contacts { position: absolute; left: 374px; top: 188px; list-style: none; }
  .contacts li { display: flex; align-items: center; height: 24px; margin-bottom: 15px; font-size: 16px; font-weight: 700; }
  .contacts svg { width: 26px; height: 24px; margin-right: 16px; flex: none; }

  .card--back .brand { left: 0; top: 80px; width: 689px; }
  .card--back .brand__dot { width: 150px; height: 150px; margin-bottom: 26px; }
  .card--back .brand__name { font-size: 24px; }

  .tagline { position: absolute; left: 0; top: 345px; width: 689px; text-align: center; font-size: 13.5px; font-weight: 700; letter-spacing: 0.06em; }
</style>
</head>
<body>
  <section class="card card--front">
    <svg class="front-wave" viewBox="0 0 689 394" aria-hidden="true">
      <path d="M0,394 C60,340 130,322 200,322 C320,322 420,355 544,353 C610,352 660,345 689,338 L689,394 Z" fill="var(--ink)"/>
    </svg>

    <div class="brand">
      <span class="brand__dot"></span>
      <span class="brand__name">TREVAN GROUNDMAKRZ LLC<br>555-714-9082</span>
    </div>

    <span class="divider"></span>

    <div class="person">
      <h1 class="person__name">DALE VORSKIN</h1>
      <span class="person__role">OWNER</span>
    </div>

    <ul class="contacts">
      <li>
        <svg viewBox="0 0 26 24" aria-hidden="true"><rect x="1" y="4" width="24" height="16" fill="var(--gold)"/><path d="M1,4 L13,14 L25,4" fill="none" stroke="var(--paper)" stroke-width="1.8"/></svg>
        @TRV-GROUNDMAKRZ.COM
      </li>
      <li>
        <svg viewBox="0 0 26 24" aria-hidden="true"><path d="M6,2 L10,7 L8,10 C9,13 12,16 15,17 L18,15 L23,19 L20,23 C11,22 3,14 2,5 Z" fill="none" stroke="var(--gold)" stroke-width="1.6" stroke-linejoin="round"/></svg>
        +555- 714-9082
      </li>
      <li>
        <svg viewBox="0 0 26 24" aria-hidden="true"><g fill="none" stroke="var(--gold)" stroke-width="1.4"><circle cx="13" cy="12" r="11"/><ellipse cx="13" cy="12" rx="5" ry="11"/><line x1="2" y1="12" x2="24" y2="12"/><line x1="4" y1="6" x2="22" y2="6"/><line x1="4" y1="18" x2="22" y2="18"/></g></svg>
        www.trv-groundmakrz.com
      </li>
    </ul>
  </section>

  <section class="card card--back">
    <div class="brand">
      <span class="brand__dot"></span>
      <span class="brand__name">TREVAN GROUNDMAKRZ LLC<br>555-714-9082</span>
    </div>
    <p class="tagline">SPEACIALIZES IN LAND CLEARING , MUCLHING AND EXCAVATION</p>
  </section>
</body>
</html>
```